Zielgruppe
Wir sind ein gemischter Chor aus der Schweiz unsere Mitglieder sind zwischen 20 und 70 Jahre jung und singen Querbeet durch die Musik von Drummel bis Lantern.
Weitere Infos www.wolkenstimmen-beispiel.ch
Aufgabenstellung
Für unser Konzert mit dem Titel " Glanzlichter Wolkenstimmen" brauchen wir für den Flyer ein Vorderseite Design. Das Konzertprogramm beinhaltet folgende Lieder:
Morgenlicht/ Varga, Bretonischer Nebel / Kai Wettbrand, Mai più qui/ Tilda,Ron+Asta, Falkachtal / Rolk,Beneath the willow/ Gaukler von Tamr, Anyone to hold/Lantern, Falling of the elk/ trad. Irl.,Danse ma rivière/trad CH,Won't you keep the fire burning bright/ Bram Feldway, Alba del mar/Driftkey, Follow the Thunder/Al Brenning.
Idealerweise nimmt das Design Bezug auf den Titel oder auf eines oder mehrere Lieder.
Format: A5 hoch
Text: "Glanzlichter Wolkenstimmen"
Samstag 7. November 2015
17.00 Uhr, Singsaal Talwacht, Uerikon / Stäfa
Sonntag 8. November 2015
17.00 Uhr Kornhaldensaal, Uetikon am See
Eintritt frei Kollekte

```html
<!DOCTYPE html>
<html lang="de">
<head>
<meta charset="utf-8">
<title>Glanzlichter Wolkenstimmen – Konzertflyer</title>
<link href="https://fonts.googleapis.com/css2?family=Open+Sans:wght@400;600;700&family=Kaushan+Script&display=swap" rel="stylesheet">
<style>
  :root {
    --maroon: #5a0a26;
    --maroon-dark: #4a0620;
    --berry: #8c1034;
    --pink-light: #fbe3e6;
    --white: #ffffff;
    --text: #4a0a20;
  }
  html, body {
    margin: 0;
    padding: 0;
    width: 800px;
    height: 1200px;
    overflow: hidden;
    background: var(--white);
  }
  .flyer {
    position: relative;
    width: 800px;
    height: 1200px;
    overflow: hidden;
    font-family: "Open Sans", Arial, sans-serif;
    color: var(--text);
    background: var(--pink-light);
  }
  .backdrop {
    position: absolute;
    inset: 0;
  }
  .title-banner {
    position: absolute;
    left: 0;
    top: 0;
    width: 800px;
    height: 300px;
  }
  .title-text {
    position: absolute;
    left: 166px;
    top: 110px;
    width: 468px;
    text-align center;
    text-align: center;
    white-space: nowrap;
    font-family: "Kaushan Script", cursive;
    font-size: 36px;
    line-height: 50px;
    color: var(--white);
    transform: rotate(2deg);
  }
  .ornament {
    position: absolute;
    left: 204px;
    width: 404px;
    height: 60px;
    border-radius: 30px;
  }
  .ornament--top {
    top: 278px;
    background: linear-gradient(90deg, rgba(255,255,255,0) 0%, rgba(255,255,255,0.75) 20%, rgba(255,255,255,0.85) 50%, rgba(255,255,255,0.75) 80%, rgba(255,255,255,0) 100%);
  }
  .ornament--bottom {
    top: 884px;
    background: linear-gradient(90deg, rgba(255,150,210,0) 0%, rgba(255,150,210,0.75) 25%, rgba(255,200,225,0.8) 50%, rgba(255,220,235,0.7) 80%, rgba(255,220,235,0) 100%);
  }
  .programme {
    position: absolute;
    left: 0;
    top: 390px;
    width: 800px;
    text-align: center;
  }
  .programme__heading {
    margin: 0 0 30px;
    font-size: 29px;
    font-weight: 700;
    color: var(--maroon-dark);
  }
  .programme__list {
    list-style: none;
    margin: 0;
    padding: 0;
    font-size: 23.5px;
    line-height: 30.6px;
    color: var(--maroon-dark);
  }
  .dates {
    position: absolute;
    right: 26px;
    top: 1014px;
    width: 530px;
    text-align: right;
  }
  .date {
    position: relative;
  }
  .date__day {
    font-size: 37px;
    font-weight: 600;
    line-height: 44px;
    color: var(--maroon);
  }
  .date__place {
    font-size: 21px;
    line-height: 22px;
    color: var(--maroon-dark);
  }
  .date + .date { margin-top: 10px; }
  .date--second .date__place { letter-spacing: 1.6px; }
  .note-icon {
    position: absolute;
    left: 0;
    top: 6px;
    width: 40px;
    height: 56px;
  }
  .admission {
    margin-top: 2px;
    font-size: 21px;
    font-weight: 700;
    color: #3a1a22;
  }
</style>
</head>
<body>
<div class="flyer">

  <svg class="backdrop" width="800" height="1200" viewBox="0 0 800 1200" xmlns="http://www.w3.org/2000/svg" role="img" aria-label="Leuchtender Farbverlauf in Rot, Orange und Pink mit hellen Lichtflecken">
    <defs>
      <radialGradient id="glow" cx="0.45" cy="0.38" r="0.7">
        <stop offset="0" stop-color="#fde7a0"/>
        <stop offset="0.25" stop-color="#f9b33a"/>
        <stop offset="0.55" stop-color="#ef4f2a"/>
        <stop offset="0.85" stop-color="#e02e3a"/>
        <stop offset="1" stop-color="#d0204a"/>
      </radialGradient>
      <linearGradient id="lowerFade" x1="0" y1="0" x2="0" y2="1">
        <stop offset="0.55" stop-color="#e0304a" stop-opacity="0"/>
        <stop offset="1" stop-color="#c41848" stop-opacity="0.85"/>
      </linearGradient>
      <radialGradient id="softLight" cx="0.5" cy="0.5" r="0.5">
        <stop offset="0" stop-color="#ffffff" stop-opacity="0.55"/>
        <stop offset="1" stop-color="#ffffff" stop-opacity="0"/>
      </radialGradient>
    </defs>
    <rect width="800" height="1200" fill="#fbe3e6"/>
    <path d="M0 240 Q400 120 800 240 L800 1200 L0 1200 Z" fill="url(#glow)"/>
    <path d="M0 240 Q400 120 800 240 L800 1200 L0 1200 Z" fill="url(#lowerFade)"/>
    <circle cx="210" cy="430" r="160" fill="url(#softLight)"/>
    <circle cx="720" cy="300" r="90" fill="url(#softLight)"/>
    <circle cx="60" cy="980" r="120" fill="url(#softLight)"/>
    <path d="M0 1035 Q420 960 800 952 L800 1200 L0 1200 Z" fill="var(--berry)"/>
    <path d="M0 1075 Q380 980 800 975 L800 1200 L0 1200 Z" fill="var(--white)"/>
  </svg>

  <svg class="title-banner" width="800" height="300" viewBox="0 0 800 300" xmlns="http://www.w3.org/2000/svg">
    <path d="M24 205 L168 140 L196 212 L76 282 L92 240 Z" fill="var(--maroon)"/>
    <path d="M776 205 L632 140 L604 212 L724 282 L708 240 Z" fill="var(--maroon)"/>
    <path d="M168 140 L196 212 L210 196 Z" fill="#2e0414"/>
    <path d="M632 140 L604 212 L590 196 Z" fill="#2e0414"/>
    <path d="M166 104 Q400 52 634 100 L612 214 Q400 168 190 212 Z" fill="var(--maroon)"/>
  </svg>
  <div class="title-text">Glanzlichter Wolkenstimmen</div>

  <div class="ornament ornament--top" role="img" aria-label="Weisses verschnörkeltes Zierornament"></div>

  <section class="programme">
    <h2 class="programme__heading">Konzertprogramm:</h2>
    <ul class="programme__list">
      <li>Morgenlicht/ Varga</li>
      <li>Bretonischer Nebel / Kai Wettbrand</li>
      <li>Mai più qui/ Tilda</li>
      <li>Ron+Asta Falkachtal / Rolk</li>
      <li>Beneath the willow/ Gaukler von Tamr</li>
      <li>Anyone to hold/Lantern</li>
      <li>Falling of the elk/ trad. Irl.</li>
      <li>Danse ma rivière/trad CH</li>
      <li>Won't you keep the fire burning bright/ Bram Feldway</li>
      <li>Alba del mar/Driftkey</li>
      <li>Follow the Thunder/Al Brenning</li>
    </ul>
  </section>

  <div class="ornament ornament--bottom" role="img" aria-label="Rosa verschnörkeltes Zierornament"></div>

  <section class="dates">
    <div class="date date--first">
      <svg class="note-icon" viewBox="0 0 40 56" xmlns="http://www.w3.org/2000/svg">
        <ellipse cx="13" cy="45" rx="12" ry="9" transform="rotate(-25 13 45)" fill="var(--maroon)"/>
        <rect x="21" y="4" width="4" height="42" fill="var(--maroon)"/>
        <path d="M25 4 Q30 16 38 20 Q34 26 36 34 Q32 24 25 20 Z" fill="var(--maroon)"/>
      </svg>
      <div class="date__day">Samstag 7. November 2015</div>
      <div class="date__place">17.00 Uhr, Singsaal Talwacht, Uerikon / Stäfa</div>
    </div>
    <div class="date date--second">
      <svg class="note-icon" viewBox="0 0 40 56" xmlns="http://www.w3.org/2000/svg">
        <ellipse cx="13" cy="45" rx="12" ry="9" transform="rotate(-25 13 45)" fill="var(--maroon)"/>
        <rect x="21" y="4" width="4" height="42" fill="var(--maroon)"/>
        <path d="M25 4 Q30 16 38 20 Q34 26 36 34 Q32 24 25 20 Z" fill="var(--maroon)"/>
      </svg>
      <div class="date__day">Sonntag 8. November 2015</div>
      <div class="date__place">17.00 Uhr Kornhaldensaal, Uetikon am See</div>
    </div>
    <div class="admission">Eintritt frei Kollekte</div>
  </section>

</div>
</body>
</html>
```